BrivoTerna. Lantern of the Steady Harvest. Business card

Professional business card for BrivoTerna (Lantern of the Steady Harvest)
My rationale: Strategy-> Execution-> Results-> Value that lead to the BrivoTerna name: We put the Lantern of the Steady Harvest.
We deliver value to our customers helping them at defining a good strategy (cyan arrow). 90% of well formulated strategies fail due to poor execution so we also consider strategical execution very important (green arrow). Due to the execution we obtain the results (blue arrow). Finally, the results provide feedback to redefine strategy, and the new strategy has to be executed and new results obtained providing new feedback and on and on. It's like a wheel that finally, must create corporate value: value for shareholders, staholders, employees, providers...-

Target Market(s)

CEOs and steering comitees , invewrnent funds

Industry/Entity Type

Business Consultant

Contact Information for Business Card

Teodoro Vinsquel
CEO & Founder
teodoro.vinsquel@brivoterna-example.com
Mobile: +34 655.803.912
www.brivoterna-example.com

Colors

Designer to choose colors to be used in the design.

Requirements
Nice to have
• Nice to hace the words: Strategy, execution, results
• Nice to vave the claim: Lantern of the Steady Harvest
• The three colors should be shown:
• cyan for STRATEGY
• green for EXECUTION
• blue for RESULTS
Should not have
• Complete black background

```html
<!DOCTYPE html>
<html lang="en">
<head>
<meta charset="utf-8">
<title>BrivoTerna Business Card</title>
<link href="https://fonts.googleapis.com/css2?family=Arimo:wght@400;700&display=swap" rel="stylesheet">
<style>
  :root {
    --bg: #e6e8eb;
    --cyan: #12a9e6;
    --green: #8dc63f;
    --blue: #1d3f9c;
    --navy: #0b2f8a;
    --grey-text: #555b63;
    --rule: #d9dcdf;
    --white: #ffffff;
  }
  * { box-sizing: border-box; margin: 0; padding: 0; }
  html, body {
    width: 1200px; height: 900px; overflow: hidden;
    background: var(--bg);
    font-family: "Arimo", Arial, sans-serif;
  }
  .canvas {
    width: 1200px; height: 900px;
    display: flex; flex-direction: column;
    align-items: center; justify-content: center; gap: 60px;
  }
  .card {
    width: 620px; height: 354px;
    border-radius: 4px;
    box-shadow: 0 10px 28px rgba(0,0,0,0.18);
    position: relative; overflow: hidden;
  }
  /* Front */
  .card-front {
    background: linear-gradient(200deg, var(--cyan) 0%, #6cc66a 38%, var(--green) 55%, #2a6fa8 78%, var(--navy) 100%);
    display: flex; flex-direction: column; align-items: center; justify-content: center;
    color: var(--white);
  }
  .front-brand {
    display: flex; align-items: center; gap: 14px;
  }
  .brand-dot {
    width: 22px; height: 22px; border-radius: 50%; background: var(--white);
  }
  .front-name {
    font-size: 62px; font-weight: 700; letter-spacing: -1px;
  }
  .front-claim {
    margin-top: 14px;
    font-size: 15px; font-weight: 700; letter-spacing: 0.5px;
    text-transform: uppercase;
  }
  /* Back */
  .card-back {
    background: var(--white);
  }
  .back-brand {
    position: absolute; left: 34px; top: 128px;
    display: flex; align-items: center; gap: 10px;
  }
  .brand-square {
    width: 18px; height: 18px; background: var(--blue);
  }
  .back-name {
    font-size: 38px; font-weight: 700; color: var(--blue); letter-spacing: -0.5px;
  }
  .divider {
    position: absolute; left: 300px; top: 46px; width: 1px; height: 150px;
    background: var(--rule);
  }
  .contact {
    position: absolute; left: 320px; top: 48px; width: 280px;
  }
  .person-name { font-size: 22px; color: var(--blue); }
  .person-role { font-size: 14px; color: var(--grey-text); margin-top: 2px; }
  .contact-list { list-style: none; margin-top: 12px; }
  .contact-list li {
    display: flex; align-items: center; gap: 7px;
    font-size: 13px; color: var(--grey-text); line-height: 20px;
  }
  .contact-list svg { width: 13px; height: 13px; fill: var(--navy); flex: none; }
  .contact-rule {
    position: absolute; left: 320px; right: 26px; top: 208px; height: 1px; background: var(--rule);
  }
  .pillars {
    position: absolute; right: 26px; bottom: 58px;
    font-size: 17px; font-weight: 700; text-transform: uppercase; letter-spacing: 0.3px;
  }
  .pillar-strategy { color: var(--blue); }
  .pillar-execution { color: var(--green); }
  .pillar-results { color: var(--cyan); }
  .base-rule {
    position: absolute; left: 26px; right: 26px; bottom: 42px; height: 1px; background: var(--rule);
  }
</style>
</head>
<body>
<main class="canvas">
  <section class="card card-front" aria-label="Card front">
    <div class="front-brand">
      <span class="brand-dot"></span>
      <span class="front-name">BrivoTerna</span>
    </div>
    <p class="front-claim">Lantern of the Steady Harvest</p>
  </section>

  <section class="card card-back" aria-label="Card back">
    <div class="back-brand">
      <span class="brand-square"></span>
      <span class="back-name">BrivoTerna</span>
    </div>
    <div class="divider"></div>
    <div class="contact">
      <p class="person-name">Teodoro Vinsquel</p>
      <p class="person-role">CEO &amp; Founder</p>
      <ul class="contact-list">
        <li>
          <svg viewBox="0 0 16 16" aria-hidden="true"><path d="M3 1h3l1.5 4-2 1.3a9 9 0 0 0 4.2 4.2L11 8.5l4 1.5v3a2 2 0 0 1-2 2A12 12 0 0 1 1 3a2 2 0 0 1 2-2z"/></svg>
          +34 655.803.912
        </li>
        <li>
          <svg viewBox="0 0 16 16" aria-hidden="true"><path d="M1 3h14v10H1z M2 4.2v.4l6 4 6-4v-.4z" fill-rule="evenodd"/></svg>
          teodoro.vinsquel@brivoterna-example.com
        </li>
        <li>
          <svg viewBox="0 0 16 16" aria-hidden="true"><circle cx="8" cy="8" r="7"/><path d="M1 8h14M8 1c-3 3.5-3 10.5 0 14M8 1c3 3.5 3 10.5 0 14" stroke="#fff" stroke-width="1" fill="none"/></svg>
          www.brivoterna-example.com
        </li>
      </ul>
    </div>
    <div class="contact-rule"></div>
    <p class="pillars">
      <span class="pillar-strategy">Strategy,</span>
      <span class="pillar-execution">Execution,</span>
      <span class="pillar-results">Results</span>
    </p>
    <div class="base-rule"></div>
  </section>
</main>
</body>
</html>
```